Homemaking training schools needs a Business Card design

Designer, Hello!

No special requirements, good-looking enough.
--------------------------------------------------------------------------

Name: Marcus Dole
Chairman
Tel: 0574-71948263
Mobile: 13857420916
Email: kelvora@mailnest.example
Web: www.prt2019.example
Add: No.258, LanpingJie, BeiyuanQu, Ningbo, Zhejiang

LOGO
Ningbo PRT Homemaking Training School

Target Market(s)

pregnant women, mothers, infants, the elderly and families, including cleaning, cooking, nursing training.

Industry/Entity Type

Business

Contact Information for Business Card

Name: Marcus Dole
Chairman
Tel: 0574-71948263
Mobile: 13857420916
Email: kelvora@mailnest.example
Web: www.prt2019.example

LOGO

Font styles to use
Serif
Sans Serif
Decorative

Requirements
Nice to have
• Feels: clean, specifications, safety, comfort, warmth and happiness.

```html
<!DOCTYPE html>
<html lang="en">
<head>
<meta charset="utf-8">
<title>PinRuiTang Business Card</title>
<link rel="stylesheet" href="https://fonts.googleapis.com/css2?family=Quicksand:wght@500;700&display=swap">
<style>
  :root {
    --magenta: #ec0f8c;
    --blue: #1f75c0;
    --white: #ffffff;
    --grey: #5a6670;
    --page: #e9e6e1;
  }
  * { margin: 0; padding: 0; box-sizing: border-box; }
  html, body { width: 1200px; height: 950px; overflow: hidden; }
  body {
    background: var(--page);
    font-family: "Quicksand", sans-serif;
    position: relative;
  }
  .card {
    position: absolute;
    left: 240px;
    width: 720px;
    height: 420px;
    border-radius: 6px;
    overflow: hidden;
    box-shadow: 0 8px 24px rgba(0,0,0,0.18);
  }
  /* front */
  .card-front { top: 40px; background: var(--magenta); color: var(--white); }
  .front-brand {
    position: absolute; left: 0; right: 0; top: 120px;
    text-align: center;
  }
  .brand-name {
    font-weight: 700; font-size: 62px; letter-spacing: -1px; line-height: 1;
  }
  .brand-rule {
    width: 380px; height: 2px; background: currentColor; margin: 12px auto 8px;
  }
  .brand-tagline { font-weight: 500; font-size: 22px; letter-spacing: 0.5px; }
  .front-web {
    position: absolute; left: 0; right: 0; top: 300px;
    text-align: center; font-size: 18px; letter-spacing: 8px; font-weight: 500;
  }
  /* back */
  .card-back { top: 490px; background: var(--white); }
  .back-shape { position: absolute; inset: 0; }
  .back-logo {
    position: absolute; left: 46px; top: 58px; color: var(--blue);
  }
  .back-logo .mark-row { display: flex; align-items: center; gap: 10px; }
  .back-logo .dot {
    width: 22px; height: 22px; border-radius: 50%; background: var(--magenta);
  }
  .back-logo .brand-name { font-size: 44px; }
  .back-logo .brand-rule { width: 270px; margin: 8px 0 6px 32px; background: var(--grey); height: 1.5px; }
  .back-logo .brand-tagline { font-size: 16px; color: var(--grey); margin-left: 110px; }
  .person { position: absolute; left: 78px; top: 230px; }
  .person-name { color: var(--blue); font-weight: 700; font-size: 30px; }
  .person-title { color: var(--magenta); font-weight: 500; font-size: 20px; margin-top: 2px; margin-left: 40px; }
  .contact {
    position: absolute; left: 430px; top: 236px; color: var(--white);
    font-weight: 500; font-size: 16px; line-height: 1.5;
  }
  .contact .address { margin-bottom: 8px; }
  .contact-row { display: flex; align-items: center; gap: 10px; }
  .contact-row svg { width: 16px; height: 16px; flex: none; }
</style>
</head>
<body>
  <section class="card card-front" aria-label="Card front">
    <div class="front-brand">
      <div class="brand-name">PinRuiTang</div>
      <div class="brand-rule"></div>
      <div class="brand-tagline">Training &amp; Services</div>
    </div>
    <div class="front-web">www.prt2019.example</div>
  </section>

  <section class="card card-back" aria-label="Card back">
    <svg class="back-shape" viewBox="0 0 720 420" width="720" height="420" aria-hidden="true">
      <path d="M430 0 L720 0 L720 420 L290 420 C255 290 290 110 430 0 Z" fill="var(--blue)"/>
      <ellipse cx="400" cy="150" rx="58" ry="46" fill="var(--magenta)"/>
    </svg>

    <div class="back-logo">
      <div class="mark-row">
        <span class="dot"></span>
        <span class="brand-name">PinRuiTang</span>
      </div>
      <div class="brand-rule"></div>
      <div class="brand-tagline">Training &amp; Services</div>
    </div>

    <div class="person">
      <div class="person-name">Marcus Dole</div>
      <div class="person-title">Chairman</div>
    </div>

    <div class="contact">
      <div class="address">No.258, LanpingJie,<br>BeiyuanQu, Ningbo, Zhejiang</div>
      <div class="contact-row">
        <svg viewBox="0 0 16 16" aria-label="Telephone"><path d="M3 2h3l1 3-2 1.5a9 9 0 0 0 4.5 4.5L11 9l3 1v3a1 1 0 0 1-1 1A12 12 0 0 1 2 3a1 1 0 0 1 1-1z" fill="currentColor"/></svg>
        <span>0574-71948263</span>
      </div>
      <div class="contact-row">
        <svg viewBox="0 0 16 16" aria-label="Mobile"><rect x="4" y="1" width="8" height="14" rx="1.5" fill="none" stroke="currentColor" stroke-width="1.6"/><circle cx="8" cy="12.5" r="0.9" fill="currentColor"/></svg>
        <span>13857420916</span>
      </div>
      <div class="contact-row">
        <svg viewBox="0 0 16 16" aria-label="Email"><rect x="1.5" y="3.5" width="13" height="9" rx="1" fill="none" stroke="currentColor" stroke-width="1.5"/><path d="M2 4l6 5 6-5" fill="none" stroke="currentColor" stroke-width="1.5"/></svg>
        <span>kelvora@mailnest.example</span>
      </div>
      <div class="contact-row">
        <svg viewBox="0 0 16 16" aria-label="Website"><circle cx="8" cy="8" r="6.5" fill="none" stroke="currentColor" stroke-width="1.4"/><path d="M1.5 8h13M8 1.5c-3 3.5-3 9.5 0 13M8 1.5c3 3.5 3 9.5 0 13" fill="none" stroke="currentColor" stroke-width="1.2"/></svg>
        <span>www.prt2019.example</span>
      </div>
    </div>
  </section>
</body>
</html>
```